Brivora Distance Learning Website

Brivora provide e-learning and mixed learning solutions for individuals, colleges, organisations and B2B.
We need a modern, light and flat website design for Brivora. We want to to see the designer incorporate user experience(UX) design elements into the AI or PSD mockups. We would like to see designs that use pastel colors that compliment yellow and black of our logo.
We want our E-learning experience to accelerate learning and for the interface to be user friendly and intuitive. We want the designs to focus on quick access to course information, course reviews, learning progress and study advice. Quick and intuitive access to all content for our clients is one of our top priorities.
We would like designs for the following project 3 pages:
1. Learner homepage dashboard (see attached screenshot).
On this page the Learners need to:
- Login
- Have quick access to Packages and Courses.
- See other recommended courses (Below Packages and Courses)
- Possibly a left hand side column/menu with thumbnail icons (See lumeqa learner dashboard screenshot)
2. Homepage
See current sample
http://www.brivora-learn.example
We would like the designer to focus on creating a customized banner to enhance the home page.
3. Primary Landing/Marketing page
This page is geared towards customer acquisition with the focal point being the top banner (video or HD image).
And Course Preview content below.
See reference
http://brivora-learn.example/subscriptionPlans/marketing/MTc%3D/Mjc4Nw%3D%3D/Speaking%20Nepali%20%2B%20Nepali%20Snacks%20Bundle%20by%20Lorne%20Pike%20Vell
Other site we like:
- https://www.skillorva.example (We like the home page and top bar on courses page)
- http://www.tutorcrest.example
- http://pixelgrovelab.example (think this site looks great, love the lower graphics on the homepage)
Updates
Hello,
Thank you for taking the time to contribute to this web design competition. We would just like to point out a few things:
1. Please try to make the color palette similar to the colors used in the screenshot that we just uploaded ('possible color palette).
2. Please make the designs specific to each page: THE LEARNER HOMEPAGE, HOME PAGE, and the MARKETING LANDING PAGE.
We are very happy with the high quality of designs so far,
Cheers,
Ned Ru
VK-Studio
Also,
Please avoid using dark/bold elements in the designs. The ONLY elements that we want to be dark are the logo and the footer.
Any questions please ask,
Cheers,
Ned Ru
Vk-Studio
Hello,
Based on the round of feedback we just gave it would be great if you could complete further design changes by tomorrow, as we are pushed for time.
Thank you,
Ned Ru
VK-Studio

```html
<!DOCTYPE html>
<html lang="en">
<head>
<meta charset="utf-8">
<title>Brivora – Learner Home</title>
<link href="https://fonts.googleapis.com/css2?family=Open+Sans:wght@400;600;700&display=swap" rel="stylesheet">
<style>
:root{
  --yellow:#f5b320;
  --yellow-dark:#d99a0c;
  --ink:#1a1a1a;
  --text:#6f6f6f;
  --link-blue:#1d4e8f;
  --band:#f1f1f1;
  --footer:#1f1f1f;
  --footer-text:#a8a8a8;
  --white:#ffffff;
}
*{margin:0;padding:0;box-sizing:border-box}
html,body{width:1171px;height:1200px;overflow:hidden;background:var(--white);font-family:"Open Sans",sans-serif}
.page{position:relative;width:1171px;height:1200px}
.abs{position:absolute}

/* sidebar */
.sidebar{left:0;top:0;width:59px;height:600px;background:var(--yellow)}
.side-item{position:absolute;left:0;width:59px;text-align:center;font-size:8.5px;line-height:11px;color:var(--ink)}
.side-item svg{display:block;margin:0 auto 2px}

/* hero */
.hero{left:59px;top:0;width:1112px;height:600px;background:linear-gradient(100deg,#6b6a66 0%,#9c9a93 30%,#d9d6cf 55%,#e9e6e1 75%,#cfcac2 100%)}
.topbar{left:129px;top:0;width:913px;height:70px;background:var(--white)}
.brand{left:142px;top:20px;display:flex;align-items:center;gap:6px;font-size:22px;font-weight:700;color:var(--ink)}
.brand-dot{width:16px;height:16px;border-radius:50%;background:var(--yellow)}
.nav{top:25px;font-size:11px;color:#6b6b6b}
.nav.active{color:var(--yellow)}
.nav-login{left:966px;top:21px;width:53px;height:25px;background:var(--yellow);border-radius:2px;font-size:11px;color:#3a2a00;text-align:center;line-height:25px}
.hero-title{left:153px;top:172px;font-size:47px;line-height:45px;font-weight:700;color:var(--white)}
.hero-btn{left:153px;top:276px;width:141px;height:42px;background:var(--yellow);border-bottom:3px solid var(--yellow-dark);font-size:14px;color:#3a2a00;text-align:center;line-height:40px}
.dots{left:547px;top:556px;width:75px;height:18px;border-radius:9px;background:rgba(60,60,60,.7);display:flex;justify-content:center;align-items:center;gap:8px}
.dots span{width:7px;height:7px;border-radius:50%;background:#eee}
.dots span.on{background:none;border:1.5px solid #eee}

/* login */
.login-box{left:143px;top:642px;width:391px;height:181px;border:1px solid var(--yellow);background:#f3f3f3}
.login-title{left:168px;top:660px;font-size:27px;font-weight:600;color:#555;display:flex;align-items:center;gap:8px}
.field{left:169px;width:261px;height:37px;background:var(--white);border:1px solid #e3e3e3;font-size:11.5px;color:#666;padding-left:15px;line-height:35px}
.login-btn{left:440px;top:758px;width:70px;height:38px;background:var(--yellow);font-size:13px;font-weight:600;color:#7a5500;text-align:center;line-height:38px}

/* welcome */
.welcome{left:558px;top:634px;font-size:27px;color:var(--yellow)}
.intro{left:558px;top:679px;width:474px;font-size:11.2px;line-height:18.8px;color:var(--text)}
.search{left:558px;top:786px;width:374px;height:38px;background:#e6e6e6;font-size:11.5px;color:#444;padding-left:15px;line-height:38px}
.search svg{position:absolute;right:16px;top:9px}

/* quick links */
.links-band{left:0;top:874px;width:1171px;height:202px;background:var(--band)}
.links-title{top:896px;font-size:13px;color:var(--link-blue)}
.link-list{top:926px;list-style:none;font-size:9.8px;line-height:20.2px;color:#666}
.link-list li::before{content:"•";font-size:8px;color:#999;margin-right:5px}
.links-divider{top:898px;width:1px;height:140px;background:#d6d6d6}

/* footer */
.footer{left:0;top:1076px;width:1171px;height:124px;background:var(--footer)}
.foot-brand{left:130px;top:1099px;width:120px;height:43px;background:#9b9b9b;display:flex;align-items:center;justify-content:center;gap:5px;font-size:19px;font-weight:700;color:var(--ink)}
.foot-brand .brand-dot{width:12px;height:12px}
.copyright{left:130px;top:1160px;font-size:10.5px;color:var(--footer-text)}
.foot-divider{left:400px;top:1084px;width:1px;height:108px;background:#3a3a3a}
.foot-nav{right:131px;top:1101px;font-size:10.4px;font-weight:600;color:var(--footer-text);word-spacing:2px}
.foot-nav .sep{margin:0 7px}
.foot-rule{left:510px;top:1134px;width:531px;height:1px;background:#3a3a3a}
.social{top:1151px;width:26px;height:26px;border-radius:50%;background:#5a5a5a}
</style>
</head>
<body>
<div class="page">

  <div class="abs hero" role="img" aria-label="Photo of a man in glasses thinking in front of a laptop in a bright bookshop"></div>

  <aside class="abs sidebar">
    <div class="side-item" style="top:24px">
      <svg width="20" height="18" viewBox="0 0 20 18"><rect y="1" width="20" height="3" fill="#1a1a1a"/><rect y="7.5" width="20" height="3" fill="#1a1a1a"/><rect y="14" width="20" height="3" fill="#1a1a1a"/></svg>Menu</div>
    <div class="side-item" style="top:86px">
      <svg width="24" height="20" viewBox="0 0 24 20"><rect x="1" y="1" width="22" height="5" fill="#1a1a1a"/><rect x="1" y="8" width="22" height="5" fill="#1a1a1a"/><rect x="1" y="15" width="22" height="4" fill="#1a1a1a"/></svg>Learning<br>Publishers<br>Dashboard</div>
    <div class="side-item" style="top:178px">
      <svg width="24" height="20" viewBox="0 0 24 20"><rect x="8" y="1" width="8" height="4" fill="none" stroke="#1a1a1a" stroke-width="2"/><rect x="1" y="5" width="22" height="14" rx="2" fill="#1a1a1a"/><rect x="1" y="10" width="22" height="1.5" fill="#f5b320"/></svg>Find<br>Learning<br>Packages</div>
    <div class="side-item" style="top:272px">
      <svg width="22" height="22" viewBox="0 0 22 22"><path d="M11 1l3 7 7 .5-5.5 4.5 2 7L11 16l-6.5 4 2-7L1 8.5 8 8z" fill="none" stroke="#1a1a1a" stroke-width="2"/></svg>Reviews &amp;<br>Comments</div>
    <div class="side-item" style="top:351px">
      <svg width="22" height="22" viewBox="0 0 22 22"><path d="M5 2h15l-3 16H2z" fill="#1a1a1a"/><path d="M6 6h10M5.5 9h10" stroke="#f5b320" stroke-width="1.3"/></svg>Purchase<br>History</div>
    <div class="side-item" style="top:436px">
      <svg width="26" height="24" viewBox="0 0 26 24"><circle cx="9" cy="14" r="6" fill="none" stroke="#1a1a1a" stroke-width="4" stroke-dasharray="3 2"/><circle cx="19" cy="6" r="4" fill="none" stroke="#1a1a1a" stroke-width="3" stroke-dasharray="2 1.5"/></svg>Settings</div>
    <div class="side-item" style="top:508px">
      <svg width="22" height="22" viewBox="0 0 22 22"><path d="M11 2c4 0 6 3 6 7v5l3 3H2l3-3V9c0-4 2-7 6-7z" fill="#1a1a1a"/><circle cx="11" cy="19.5" r="2" fill="#1a1a1a"/></svg>Notifications</div>
  </aside>

  <header>
    <div class="abs topbar"></div>
    <div class="abs brand"><span class="brand-dot"></span>Brivora</div>
    <span class="abs nav active" style="left:683px">PACKAGES</span>
    <span class="abs nav" style="left:766px">COURSES</span>
    <span class="abs nav" style="left:842px">TRIAL</span>
    <span class="abs nav" style="left:899px">REGISTER</span>
    <span class="abs nav-login">LOGIN</span>
  </header>

  <h1 class="abs hero-title">Vestibulum<br>condimentum sem</h1>
  <div class="abs hero-btn">Get Started Now</div>
  <div class="abs dots"><span class="on"></span><span></span><span></span><span></span></div>

  <section>
    <div class="abs login-box"></div>
    <div class="abs login-title">
      <svg width="18" height="22" viewBox="0 0 18 22"><path d="M4 9V6a5 5 0 0 1 10 0" fill="none" stroke="#555" stroke-width="2.5"/><rect x="1" y="9" width="16" height="12" rx="1.5" fill="#555"/></svg>Login</div>
    <div class="abs field" style="top:710px">E-mail</div>
    <div class="abs field" style="top:758px">Password</div>
    <div class="abs login-btn">LOGIN</div>

    <h2 class="abs welcome" style="font-weight:400">Welcome to Brivora</h2>
    <p class="abs intro">Aenean facilisis tincidunt lectus, id dictum nisi luctus eget. Vivamus efficitur ex condimentum, malesuada eros eget, feugiat nibh. Sed tellus ex, imperdiet eget gravida sit amet, volutpat eget turpis. In nec ultricies est. Etiam mattis augue vehicula odio posuere, sit amet tempus lectus luctus. Nulla facilisi. Etiam vel massa elementum, bibendum tellus venenatis, feugiat massa convallis molestie enim sit amet.</p>
    <div class="abs search">Search Courses her...
      <svg width="20" height="20" viewBox="0 0 20 20"><circle cx="8" cy="8" r="6" fill="none" stroke="#555" stroke-width="2.5"/><path d="M12.5 12.5l6 6" stroke="#555" stroke-width="3"/></svg></div>
  </section>

  <section>
    <div class="abs links-band"></div>
    <h3 class="abs links-title" style="left:138px;font-weight:400">Quick Links</h3>
    <ul class="abs link-list" style="left:138px"><li>Integer lobortis</li><li>Curabitur ac</li><li>Phasellus tellus nisl</li><li>Aenean fringilla</li><li>Vestibulum</li><li>Aliquam commodo</li></ul>
    <ul class="abs link-list" style="left:290px"><li>Integer lobortis</li><li>Curabitur ac</li><li>Phasellus tellus nisl</li><li>Aenean fringilla</li><li>Vestibulum</li><li>Aliquam commodo</li></ul>
    <div class="abs links-divider" style="left:430px"></div>
    <h3 class="abs links-title" style="left:470px;font-weight:400">Quick Links</h3>
    <ul class="abs link-list" style="left:470px"><li>Integer lobortis</li><li>Curabitur ac</li><li>Phasellus tellus nisl</li><li>Aenean fringilla</li><li>Vestibulum</li><li>Aliquam commodo</li></ul>
    <ul class="abs link-list" style="left:621px"><li>Integer lobortis</li><li>Curabitur ac</li><li>Phasellus tellus nisl</li><li>Aenean fringilla</li><li>Vestibulum</li><li>Aliquam commodo</li></ul>
    <div class="abs links-divider" style="left:758px"></div>
    <h3 class="abs links-title" style="left:798px;font-weight:400">Quick Links</h3>
    <ul class="abs link-list" style="left:798px"><li>Integer lobortis</li><li>Curabitur ac</li><li>Phasellus tellus nisl</li><li>Aenean fringilla</li><li>Vestibulum</li><li>Aliquam commodo</li></ul>
    <ul class="abs link-list" style="left:948px"><li>Integer lobortis</li><li>Curabitur ac</li><li>Phasellus tellus nisl</li><li>Aenean fringilla</li><li>Vestibulum</li><li>Aliquam commodo</li></ul>
  </section>

  <footer>
    <div class="abs footer"></div>
    <div class="abs foot-brand"><span class="brand-dot"></span>Brivora</div>
    <p class="abs copyright">Copyright © 2015 Brivora. All rights reserved.</p>
    <div class="abs foot-divider"></div>
    <nav class="abs foot-nav">Home<span class="sep">|</span>Pages<span class="sep">|</span>Courses<span class="sep">|</span>Trial<span class="sep">|</span>Register<span class="sep">|</span>Login<span class="sep">|</span>Terms of Service<span class="sep">|</span>Privacy Policy</nav>
    <div class="abs foot-rule"></div>
    <span class="abs social" style="left:858px"></span>
    <span class="abs social" style="left:889px"></span>
    <span class="abs social" style="left:920px"></span>
    <span class="abs social" style="left:952px"></span>
    <span class="abs social" style="left:983px"></span>
    <span class="abs social" style="left:1014px"></span>
  </footer>

</div>
</body>
</html>
```